Vantiqo custom business card design

Need a authentic, innovative business card design for a new mobile app business. I am uploading a few screen images from our app for you to view. I would like app design theme to match business card design. I can also send logo images.

```html
<!DOCTYPE html>
<html lang="en">
<head>
<meta charset="utf-8">
<title>Vantiqo Business Card</title>
<link href="https://fonts.googleapis.com/css2?family=Open+Sans:wght@400;600;700;800&display=swap" rel="stylesheet">
<style>
  :root {
    --purple: #5e0a93;
    --purple-deep: #4a0776;
    --purple-light: #7a1bb8;
    --ink: #1d1d1d;
    --grey-text: #3a3a3a;
    --tint: #ece6f1;
    --backdrop: #e4e4e6;
    --white: #ffffff;
  }
  * { margin: 0; padding: 0; box-sizing: border-box; }
  html, body {
    width: 1200px; height: 1000px; overflow: hidden;
    background: var(--backdrop);
    font-family: "Open Sans", Arial, sans-serif;
  }
  .stage { position: relative; width: 1200px; height: 1000px; }

  .card {
    position: absolute; left: 215px; width: 770px; height: 440px;
    overflow: hidden; border-radius: 4px;
    box-shadow: 0 10px 28px rgba(0,0,0,.18);
  }

  /* Back side */
  .card-back {
    top: 40px;
    background: linear-gradient(120deg, var(--purple-light) 0%, var(--purple) 55%, var(--purple-deep) 100%);
    display: flex; flex-direction: column; align-items: center; justify-content: center;
  }
  .back-mark { display: flex; align-items: center; gap: 18px; }
  .back-dot { width: 46px; height: 46px; border-radius: 50%; background: var(--white); }
  .back-name { color: var(--white); font-weight: 700; font-size: 58px; letter-spacing: 1px; }
  .back-url {
    position: absolute; bottom: 40px; color: var(--white);
    font-size: 20px; letter-spacing: 7px; font-weight: 400;
  }

  /* Front side */
  .card-front { top: 520px; background: var(--white); }
  .front-decor {
    position: absolute; right: -120px; top: 40px;
    width: 520px; height: 520px; border-radius: 50%;
    background: linear-gradient(135deg, #efeff1 0%, var(--tint) 100%);
  }
  .front-decor::after {
    content: ""; position: absolute; left: 120px; top: 120px;
    width: 280px; height: 280px; border-radius: 50%; background: #f6f6f7;
  }
  .brand { position: absolute; left: 44px; top: 38px; display: flex; align-items: center; gap: 12px; }
  .brand-dot { width: 30px; height: 30px; border-radius: 50%; background: var(--purple); }
  .brand-name { font-weight: 800; font-size: 38px; color: var(--ink); }

  .contact { position: absolute; left: 44px; top: 120px; color: var(--grey-text); font-size: 19px; line-height: 1.42; }
  .address { margin-bottom: 6px; }
  .contact-list { list-style: none; }
  .contact-list li { display: flex; align-items: center; gap: 12px; }
  .contact-list svg { width: 18px; height: 18px; fill: var(--purple); flex: none; }

  .person { position: absolute; right: 60px; bottom: 90px; text-align: left; }
  .person-name { color: var(--purple); font-weight: 700; font-size: 28px; letter-spacing: .5px; }
  .person-title { color: var(--ink); font-size: 22px; letter-spacing: .5px; margin-top: -4px; }
</style>
</head>
<body>
<main class="stage">
  <section class="card card-back">
    <div class="back-mark">
      <span class="back-dot"></span>
      <span class="back-name">Vantiqo</span>
    </div>
    <p class="back-url">vantiqo.com</p>
  </section>

  <section class="card card-front">
    <div class="front-decor"></div>

    <div class="brand">
      <span class="brand-dot"></span>
      <span class="brand-name">Vantiqo</span>
    </div>

    <div class="contact">
      <p class="address">2170 Harwell Avenue<br>Brookdale, NY 11920</p>
      <ul class="contact-list">
        <li><svg viewBox="0 0 20 20"><path d="M2 7c0-3 3-4 8-4s8 1 8 4v2h-4V7H6v2H2zM5 10h10l2 7H3z"/></svg>555 0142 7310</li>
        <li><svg viewBox="0 0 20 20"><path d="M6 1h8a1 1 0 0 1 1 1v16a1 1 0 0 1-1 1H6a1 1 0 0 1-1-1V2a1 1 0 0 1 1-1zm1 2v12h6V3z"/></svg>555 0187 2964</li>
        <li><svg viewBox="0 0 20 20"><path d="M5 2h8l2 2v4H5zM2 9h16v7h-3v3H5v-3H2zm5 5v3h6v-3z"/></svg>555 0163 4821</li>
        <li><svg viewBox="0 0 20 20"><path d="M1 4h18v2l-9 6-9-6zm0 4 9 6 9-6v8H1z"/></svg>mara@vantiqo.com</li>
        <li><svg viewBox="0 0 20 20"><circle cx="10" cy="10" r="9"/></svg>www.vantiqo.com</li>
      </ul>
    </div>

    <div class="person">
      <p class="person-name">MARA LIND</p>
      <p class="person-title">PRESIDENT</p>
    </div>
  </section>
</main>
</body>
</html>
```